Spring Detox sale graphics for social media

You MUST read the Brief in the WORD document and follow the instructions there. I want to create 10 social media graphics (new Instagram size 4:5 (1080 x 1350 pixels) focusing on our Mother’s Day Spring Detox Sale graphics, using any of the pics attached. Use the attached pics, NO RANDOM STOCK PHOTOGRAPHY. For the color scheme of the graphics, they should all be complementary to the product colors or feel like Spring time.

Target Market(s)

primarily women

Requirements
Must have
• the photos and text attached

```html
<!DOCTYPE html>
<html lang="en">
<head>
<meta charset="utf-8">
<title>Mother's Day Spring Detox Sale</title>
<link href="https://fonts.googleapis.com/css2?family=Montserrat:wght@300;700&family=EB+Garamond:wght@400&display=swap" rel="stylesheet">
<style>
  :root {
    --edge-blue: #5b74e9;
    --deep-blue: #2a2fa8;
    --deep-blue-dark: #1f2496;
    --glow-blue: rgba(120, 140, 240, 0.28);
    --card-white: #ffffff;
    --card-shade: #eeeeef;
    --ink-navy: #2a2fa3;
    --ink-periwinkle: #4657c6;
    --pin-red: #e3262a;
    --pin-red-light: #f04a4d;
  }
  html, body {
    margin: 0;
    padding: 0;
    width: 960px;
    height: 1200px;
    overflow: hidden;
  }
  .poster {
    position: relative;
    width: 960px;
    height: 1200px;
    box-sizing: border-box;
    border: 14px solid var(--edge-blue);
    background: linear-gradient(160deg, var(--deep-blue) 0%, var(--deep-blue-dark) 100%);
    overflow: hidden;
  }
  .backdrop {
    position: absolute;
    inset: 0;
  }
  .sale-frame {
    position: absolute;
    left: 86px;
    top: 263px;
    width: 759px;
    height: 703px;
    box-sizing: border-box;
    border: 14px solid var(--edge-blue);
    border-radius: 8px;
  }
  .sale-card {
    position: absolute;
    left: 137px;
    top: 310px;
    width: 658px;
    height: 610px;
    border-radius: 12px;
    background: linear-gradient(135deg, var(--card-white) 0%, var(--card-white) 45%, var(--card-shade) 100%);
    box-shadow: 0 2px 6px rgba(0,0,0,0.12);
  }
  .pin-placeholder {
    position: absolute;
    left: 448px;
    top: 255px;
    width: 70px;
    height: 100px;
    border-radius: 10px;
    background: linear-gradient(160deg, var(--pin-red-light) 0%, var(--pin-red) 100%);
  }
  .headline {
    position: absolute;
    left: 0;
    width: 932px;
    margin: 0;
    text-align: center;
    line-height: 1;
    white-space: nowrap;
  }
  .offer {
    top: 412px;
    font-family: "Montserrat", sans-serif;
    font-weight: 700;
    font-size: 74px;
    color: var(--ink-navy);
  }
  .occasion {
    font-family: "Montserrat", sans-serif;
    font-weight: 300;
    font-size: 79px;
    color: var(--ink-periwinkle);
  }
  .occasion-day { top: 510px; }
  .occasion-sale { top: 594px; }
  .tagline {
    top: 684px;
    font-family: "EB Garamond", serif;
    font-weight: 400;
    font-size: 50px;
    color: var(--ink-navy);
  }
  .goal {
    top: 756px;
    font-family: "Montserrat", sans-serif;
    font-weight: 700;
    font-size: 67px;
    color: var(--ink-navy);
  }
</style>
</head>
<body>
  <main class="poster">
    <svg class="backdrop" width="932" height="1172" viewBox="0 0 932 1172" aria-hidden="true">
      <circle cx="500" cy="470" r="400" fill="var(--glow-blue)" opacity="0.45"/>
      <circle cx="90" cy="400" r="185" fill="var(--glow-blue)"/>
      <circle cx="795" cy="205" r="54" fill="var(--glow-blue)"/>
    </svg>

    <div class="sale-frame"></div>
    <div class="sale-card"></div>

    <div class="pin-placeholder" role="img" aria-label="Red push pin holding the sale note"></div>

    <h1 class="headline offer">25% OFF</h1>
    <p class="headline occasion occasion-day">MOTHER’S DAY</p>
    <p class="headline occasion occasion-sale">SALE</p>
    <p class="headline tagline">Spring Detox for a</p>
    <p class="headline goal">SUMMER BODY</p>
  </main>
</body>
</html>
```